Indy Film Production Company/Studio

We need a business card designed from an existing logo. We are a digital studio/production company that caters to creating genre entertainment, like Action, Horror, and martial arts. The card along with the logo will be used to Brand the company from letter heads to banners. The design will also be used for postcards and Brochures. It should be professional and masculine.
Updates

Thank you to all the designers who have participated. I'm narrowing down who it will be. Thank you again.

Target Market(s)

Investors, Networks, Producers, and actors

Industry/Entity Type

Film Production

Contact Information for Business Card

Teodoro Valbuena
Producer/Writer/Director
www.kestrelpicturehouse.example

Requirements
Must have
• Website address, Facebook icon and Twitter icon possibly in the back of the card.
Nice to have
• Logline of Company: Follow The Action.

```html
<!DOCTYPE html>
<html lang="en">
<head>
<meta charset="utf-8">
<title>Kestrel Picture House — Business Card</title>
<link rel="stylesheet" href="https://fonts.googleapis.com/css2?family=Open+Sans:ital,wght@0,400;0,700;1,400;1,700&display=swap">
<style>
  :root {
    --backdrop: #d8d3cc;
    --card: #f3f2f0;
    --brand-red: #d3222a;
    --ink: #1c1c1c;
    --ink-soft: #333333;
    --divider: #6b6b6b;
    --band-dark: #141414;
  }
  * { margin: 0; padding: 0; box-sizing: border-box; }
  html, body {
    width: 1200px; height: 969px; overflow: hidden;
    background: var(--backdrop);
    font-family: "Open Sans", Arial, sans-serif;
  }
  .canvas { position: relative; width: 1200px; height: 969px; }
  .card {
    position: absolute; left: 100px; top: 201px;
    width: 1000px; height: 567px;
    background: var(--card);
    box-shadow: 0 10px 30px rgba(0,0,0,0.18);
    overflow: hidden;
  }
  .brand-name {
    position: absolute; left: 82px; top: 240px; width: 360px;
    color: var(--brand-red);
    font-weight: 700; font-size: 40px; line-height: 1.15;
    letter-spacing: 1px; text-transform: uppercase; text-align: center;
  }
  .divider {
    position: absolute; left: 484px; top: 195px;
    width: 2px; height: 227px; background: var(--divider);
  }
  .contact { position: absolute; left: 524px; top: 205px; }
  .contact-name {
    color: var(--brand-red);
    font-weight: 700; font-style: italic; font-size: 33px;
    text-transform: uppercase; line-height: 1.2;
  }
  .contact-role {
    color: var(--ink); font-size: 25px; text-transform: uppercase;
    line-height: 1.2; margin-top: 2px;
  }
  .contact-list { list-style: none; margin-top: 20px; }
  .contact-item {
    display: flex; align-items: center; gap: 14px;
    color: var(--ink-soft); font-size: 25px; line-height: 40px;
  }
  .contact-item.is-italic { font-style: italic; }
  .contact-icon { width: 22px; height: 22px; flex: none; fill: var(--brand-red); }
  .footer-band { position: absolute; left: 0; bottom: 0; width: 1000px; height: 25px; }
</style>
</head>
<body>
<div class="canvas">
  <div class="card">
    <div class="brand-name">Kestrel<br>Picture House</div>
    <div class="divider"></div>
    <div class="contact">
      <div class="contact-name">Teodoro Valbuena</div>
      <div class="contact-role">Producer/Writer/Director</div>
      <ul class="contact-list">
        <li class="contact-item">
          <svg class="contact-icon" viewBox="0 0 24 24" aria-hidden="true"><path d="M3 8c0-2 4-4 9-4s9 2 9 4v2h-5V8c-1-.6-2.4-1-4-1s-3 .4-4 1v2H3z M6 11h12l2 9H4z M12 13a3 3 0 1 0 0 6 3 3 0 0 0 0-6z"/></svg>
          <span>555 0142 7781</span>
        </li>
        <li class="contact-item is-italic">
          <svg class="contact-icon" viewBox="0 0 24 24" aria-hidden="true"><path d="M2 5h20v14H2z" fill="none"/><path d="M2 6h20v12H2z M2 6l10 7 10-7" /><path d="M3 7l9 6 9-6" fill="none" stroke="#f3f2f0" stroke-width="1.6"/></svg>
          <span>teo@kestrelpicturehouse.example</span>
        </li>
        <li class="contact-item is-italic">
          <svg class="contact-icon" viewBox="0 0 24 24" aria-hidden="true"><circle cx="12" cy="12" r="10"/><path d="M7 9l4 2-1 4 3 3M14 5l1 4 4 1" fill="none" stroke="#f3f2f0" stroke-width="1.6"/></svg>
          <span>www.kestrelpicturehouse.example</span>
        </li>
      </ul>
    </div>
    <svg class="footer-band" viewBox="0 0 1000 25" aria-hidden="true">
      <polygon points="0,0 775,0 760,25 0,25" fill="var(--brand-red)"/>
      <polygon points="781,0 1000,0 1000,25 766,25" fill="var(--band-dark)"/>
    </svg>
  </div>
</div>
</body>
</html>
```